New stationary design for online film company

We need some new stationary to fit with our new logo. The stationary should be professional, clean and simple.
We need designs for a full set of business stationary.
We need - letterhead, envelopes, invoices, proposals, coverslip/note and cover page

Industry/Entity Type

Business

```html
<!DOCTYPE html>
<html lang="en">
<head>
<meta charset="utf-8">
<title>lumenreel stationery set</title>
<link href="https://fonts.googleapis.com/css2?family=Open+Sans:wght@400;600;700&display=swap" rel="stylesheet">
<style>
:root{
  --bg:#d8d4cf;
  --paper:#ffffff;
  --brand-light:#6fa5c0;
  --brand-dark:#0b4770;
  --ink:#2b2b2b;
  --muted:#7aa9c1;
  --faint:#eef1f3;
}
*{box-sizing:border-box;margin:0;padding:0}
html,body{width:1200px;height:767px;overflow:hidden;background:var(--bg);font-family:"Open Sans",sans-serif;color:var(--ink)}
.canvas{position:relative;width:1200px;height:767px}
.sheet{position:absolute;background:var(--paper);box-shadow:0 1px 4px rgba(0,0,0,.25);overflow:hidden}
.brand{display:flex;align-items:center;gap:6px;font-family:"Open Sans",sans-serif;font-weight:600;color:var(--brand-light);letter-spacing:-.5px;line-height:1;white-space:nowrap}
.brand-dot{border-radius:50%;border:4px solid var(--brand-dark);flex:none}
.footer-band{position:absolute;left:0;bottom:0;width:100%}
.footer-web{position:absolute;color:#fff;font-size:8px;letter-spacing:1.6px;font-weight:600;white-space:nowrap}

/* letterhead */
.letterhead{left:12px;top:16px;width:519px;height:734px}
.letterhead .brand{position:absolute;left:174px;top:42px;font-size:28px}
.letterhead .brand-dot{width:30px;height:30px}
.contact{position:absolute;left:414px;top:28px;border-left:1px solid #bbb;padding-left:5px;font-size:5.6px;line-height:8.4px;color:#444;white-space:nowrap}
.contact p.gap{margin-top:4px}
.letterhead .footer-web{right:96px;bottom:7px}

/* cards */
.card-front{left:584px;top:14px;width:220px;height:125px}
.card-front .deco{position:absolute;left:68px;top:20px;width:82px;height:82px;border-radius:50%;border:9px solid var(--faint)}
.card-front .brand{position:absolute;left:20px;top:42px;font-size:35px;letter-spacing:-1px}
.card-front .card-web{position:absolute;left:0;width:100%;bottom:4px;text-align:center;font-size:5px;letter-spacing:1.6px;color:#555}
.card-back{left:816px;top:15px;width:221px;height:126px}
.card-back .brand{position:absolute;left:20px;top:52px;font-size:15px;gap:3px}
.card-back .brand-dot{width:15px;height:15px;border-width:2px}
.card-back .divider{position:absolute;left:120px;top:22px;width:1px;height:82px;background:#bbb}
.card-back .person{position:absolute;left:128px;top:20px;font-size:5.4px;line-height:9.6px;color:#444;white-space:nowrap}
.person .name{font-size:8px;font-weight:700;color:var(--brand-dark);line-height:9px}
.person .role{font-size:6px;color:var(--muted);margin-bottom:4px;line-height:8px}
.card-back .footer-web{right:22px;bottom:1px;font-size:5px;letter-spacing:1px}

/* envelopes */
.env-back{left:582px;top:156px;width:597px;height:196px;box-shadow:none}
.env-plain{left:570px;top:352px;width:597px;height:268px;border:1px solid #555;box-shadow:none}
.env-front{left:590px;top:461px;width:597px;height:267px}
.env-front .brand{position:absolute;left:26px;top:16px;font-size:28px}
.env-front .brand-dot{width:30px;height:30px}
.env-front .address{position:absolute;left:25px;top:74px;font-size:8.6px;letter-spacing:.8px;white-space:nowrap}
.env-front .deco{position:absolute;left:516px;top:175px;width:56px;height:56px;border-radius:50%;border:7px solid var(--faint)}
.env-front .footer-web{right:96px;bottom:8px}
</style>
</head>
<body>
<div class="canvas">

  <section class="sheet letterhead" aria-label="Letterhead">
    <div class="brand"><span class="brand-dot"></span>lumenreel</div>
    <div class="contact">
      <p>&#9742; 123-456-7890</p>
      <p>&#9993; info@lumenreel.com</p>
      <p class="gap">00, Complex Name</p>
      <p>street, city 000452</p>
    </div>
    <svg class="footer-band" width="519" height="24" viewBox="0 0 519 24">
      <polygon points="0,12 262,12 253,24 0,24" fill="var(--brand-light)"/>
      <polygon points="258,24 276,0 519,0 519,24" fill="var(--brand-dark)"/>
    </svg>
    <span class="footer-web">www.lumenreel.com</span>
  </section>

  <section class="sheet card-front" aria-label="Business card front">
    <span class="deco"></span>
    <div class="brand">lumenreel</div>
    <p class="card-web">www.lumenreel.com</p>
  </section>

  <section class="sheet card-back" aria-label="Business card back">
    <div class="brand"><span class="brand-dot"></span>lumenreel</div>
    <span class="divider"></span>
    <div class="person">
      <p class="name">Your Name</p>
      <p class="role">Designation</p>
      <p>&#9742; 123-456-7890</p>
      <p>&#9743; 123-456-7890</p>
      <p>&#9993; info@lumenreel.com</p>
      <p style="margin-top:3px">00, Complex Name</p>
      <p>street, city 000452</p>
    </div>
    <svg class="footer-band" width="221" height="10" viewBox="0 0 221 10">
      <polygon points="0,6 116,6 113,10 0,10" fill="var(--brand-light)"/>
      <polygon points="114,10 122,0 221,0 221,10" fill="var(--brand-dark)"/>
    </svg>
    <span class="footer-web">www.lumenreel.com</span>
  </section>

  <section class="sheet env-back" aria-label="Envelope flaps">
    <svg width="597" height="196" viewBox="0 0 597 196">
      <path d="M0 0H597V12Q590 50 545 58L440 81H157L52 58Q7 50 0 12Z" fill="var(--brand-light)"/>
      <path d="M0 81H597V90Q592 120 560 128L320 184Q298 189 276 184L37 128Q5 120 0 90Z" fill="var(--brand-dark)"/>
      <circle cx="298" cy="46" r="17" fill="none" stroke="#fff" stroke-width="4"/>
      <circle cx="298" cy="138" r="17" fill="none" stroke="#fff" stroke-width="4"/>
    </svg>
  </section>

  <section class="sheet env-plain" aria-label="Envelope back">
    <svg width="597" height="268" viewBox="0 0 597 268">
      <path d="M1 0V12Q4 45 40 55L275 104Q298 109 321 104L556 55Q592 45 595 12V0" fill="none" stroke="#444" stroke-width="1"/>
      <circle cx="298" cy="58" r="16" fill="none" stroke="var(--brand-dark)" stroke-width="4"/>
    </svg>
  </section>

  <section class="sheet env-front" aria-label="Envelope front">
    <div class="brand"><span class="brand-dot"></span>lumenreel</div>
    <p class="address">00, Complex Name, street, city 000452</p>
    <span class="deco"></span>
    <svg class="footer-band" width="597" height="26" viewBox="0 0 597 26">
      <polygon points="0,13 300,13 290,26 0,26" fill="var(--brand-light)"/>
      <polygon points="296,26 316,0 597,0 597,26" fill="var(--brand-dark)"/>
    </svg>
    <span class="footer-web">www.lumenreel.com</span>
  </section>

</div>
</body>
</html>
```